Tallowmere Comfort Business Card Design

Design new, 2 sides, business cards for a residential and light commercial heating, air conditioning contractor.

Target Market(s)

Homeowners, small businesses

Industry/Entity Type

Business

Contact Information for Business Card

Dominic Westerhall
Phone - 862-415-2736
Email
Address - PO box 518
Brightwater NJ 07912
Website - www.TallowmereComfortLLC.example

Requirements
Must have
• logo, company colors, standard size with no die cut, so I can use nova stamp

```html
<!DOCTYPE html>
<html lang="en">
<head>
<meta charset="utf-8">
<title>Tallowmere Comfort Business Card</title>
<link rel="stylesheet" href="https://fonts.googleapis.com/css2?family=Barlow+Semi+Condensed:wght@400;500;600&family=Roboto:wght@400&display=swap">
<style>
  :root {
    --backdrop: #e6e6e6;
    --maroon: #862a2f;
    --maroon-dark: #6e1f26;
    --cream: #f6e6b8;
    --band-gold: #e2b21a;
    --ink: #3a1a1c;
    --paper: #f7f7f5;
    --icon-red: #c8322b;
    --body-text: #4a2a2e;
  }
  * { margin: 0; padding: 0; box-sizing: border-box; }
  html, body {
    width: 1200px;
    height: 576px;
    overflow: hidden;
    background: var(--backdrop);
  }
  .sheet {
    position: relative;
    width: 1200px;
    height: 576px;
  }
  .card {
    position: absolute;
    top: 138px;
    box-shadow: 0 2px 5px rgba(0,0,0,0.25);
  }
  /* Front side */
  .card-front {
    left: 81px;
    width: 485px;
    height: 294px;
    background: var(--maroon);
  }
  .card-front .brand-name {
    position: absolute;
    left: 0;
    right: 0;
    top: 84px;
    text-align: center;
    font-family: "Barlow Semi Condensed", sans-serif;
    font-weight: 600;
    font-size: 44px;
    line-height: 48px;
    letter-spacing: 0.5px;
    color: var(--cream);
  }
  .service-band {
    position: absolute;
    left: 0;
    right: 0;
    top: 250px;
    height: 21px;
    background: var(--band-gold);
    font-family: "Roboto", sans-serif;
    font-size: 11.5px;
    line-height: 21px;
    text-align: center;
    color: var(--ink);
  }
  /* Back side */
  .card-back {
    left: 602px;
    width: 482px;
    height: 292px;
    background: var(--paper);
    font-family: "Barlow Semi Condensed", sans-serif;
  }
  .card-back .brand-name {
    position: absolute;
    left: 30px;
    width: 200px;
    top: 108px;
    text-align: center;
    font-weight: 600;
    font-size: 32px;
    line-height: 36px;
    color: var(--maroon);
  }
  .brand-line { display: block; }
  .holder {
    position: absolute;
    left: 254px;
    top: 82px;
  }
  .holder-name {
    font-weight: 600;
    font-size: 17px;
    color: var(--maroon-dark);
  }
  .holder-title {
    font-size: 11.5px;
    color: var(--body-text);
    margin-top: 1px;
  }
  .contact-list {
    position: absolute;
    left: 254px;
    top: 140px;
    list-style: none;
  }
  .contact-list li {
    display: flex;
    align-items: center;
    height: 16.5px;
    font-size: 12px;
    color: var(--body-text);
    white-space: nowrap;
  }
  .contact-list svg {
    width: 11px;
    height: 11px;
    margin-right: 13px;
    flex: none;
  }
  .base-strip {
    position: absolute;
    left: 0;
    right: 0;
    bottom: 0;
    height: 7px;
    background: var(--maroon);
  }
</style>
</head>
<body>
<main class="sheet">
  <section class="card card-front" aria-label="Card front">
    <div class="brand-name"><span class="brand-line">Tallowmere</span><span class="brand-line">Comfort</span></div>
    <div class="service-band">Residential &amp; Light Commercial Heating &nbsp;• Air Conditioning Contractor</div>
  </section>

  <section class="card card-back" aria-label="Card back">
    <div class="brand-name"><span class="brand-line">Tallowmere</span><span class="brand-line">Comfort</span></div>
    <div class="holder">
      <div class="holder-name">Dominic Westerhall</div>
      <div class="holder-title">Managing Director</div>
    </div>
    <ul class="contact-list">
      <li>
        <svg viewBox="0 0 12 12" aria-hidden="true"><path fill="var(--icon-red)" d="M1 4c0-2 2-3 5-3s5 1 5 3l-2 1-1-1.5H4L3 5zM3 6h6l1 5H2z"/></svg>
        862-415-2736
      </li>
      <li>
        <svg viewBox="0 0 12 12" aria-hidden="true"><rect x="0.5" y="2" width="11" height="8" fill="var(--icon-red)"/><path d="M1 2.5l5 4 5-4" stroke="#fff" stroke-width="1" fill="none"/></svg>
        info@TallowmereComfortLLC.example
      </li>
      <li>
        <svg viewBox="0 0 12 12" aria-hidden="true"><g fill="none" stroke="var(--icon-red)" stroke-width="1"><circle cx="6" cy="6" r="5"/><ellipse cx="6" cy="6" rx="2.2" ry="5"/><path d="M1 6h10"/></g></svg>
        www.TallowmereComfortLLC.example
      </li>
      <li>
        <svg viewBox="0 0 12 12" aria-hidden="true"><path fill="var(--icon-red)" d="M6 0.5a4 4 0 0 1 4 4c0 3-4 7-4 7s-4-4-4-7a4 4 0 0 1 4-4z"/><circle cx="6" cy="4.5" r="1.5" fill="#fff"/></svg>
        PO box 518 Brightwater NJ 07912
      </li>
    </ul>
    <div class="base-strip"></div>
  </section>
</main>
</body>
</html>
```